Need Help having my business card stand out

I am the owner of Birchway Canine Training and would like for my business cards to stand out. I have been trying to keep designing them myself but I can't get what I have in my head on the card. I will try my best to post templates that I like for inspirations. I want something unique but elegant. I don't want in to look cartoony or cheesy. It needs to pop in a pet shop but also in a coffee shop or gym.

Target Market(s)

Dog owners, Married ,No young kids Jr High school kids and up (maybe kids on the way) Executives, Stay at home moms/wives, Small business owners

Industry/Entity Type

Dog Training

Contact Information for Business Card

Lowell Spratt, 281-904-3376, info@birchwaycanine.example, www.birchwaycanine.example

Colors

Designer to choose colors to be used in the design.

Requirements
Must have
• my logo
Should not have
• Cursive lettering

```html
<!DOCTYPE html>
<html lang="en">
<head>
<meta charset="utf-8">
<title>Birchway Canine Training – Business Card</title>
<link rel="stylesheet" href="https://fonts.googleapis.com/css2?family=Open+Sans:wght@400;600;700;800&display=swap">
<style>
  :root {
    --bg: #e4e4e4;
    --card-white: #ffffff;
    --ink: #1e1e1e;
    --ink-soft: #5a5a5a;
    --ink-muted: #8a8a8a;
    --dark-1: #2c2c2c;
    --dark-2: #5c5c5c;
    --dark-3: #8e8e8e;
    --band-light: #d8d8d8;
  }
  * { box-sizing: border-box; margin: 0; padding: 0; }
  html, body { width: 1200px; height: 856px; overflow: hidden; }
  body {
    background: var(--bg);
    font-family: "Open Sans", Arial, sans-serif;
    display: flex;
    align-items: center;
    justify-content: center;
    gap: 60px;
  }
  .card {
    position: relative;
    width: 525px;
    height: 300px;
    border-radius: 30px;
    overflow: hidden;
    box-shadow: 0 14px 30px rgba(0,0,0,.18);
  }

  /* Front */
  .card--front { background: var(--card-white); }
  .front__brand {
    position: absolute;
    left: 34px; top: 0; width: 210px; height: 260px;
    display: flex; align-items: center; gap: 12px;
  }
  .brand__square { width: 18px; height: 18px; background: var(--ink); flex: none; }
  .brand__name {
    font-weight: 800; font-size: 22px; line-height: 1.15;
    color: var(--ink); letter-spacing: .2px;
  }
  .front__divider {
    position: absolute; left: 262px; top: 44px; width: 2px; height: 170px;
    background: linear-gradient(to bottom, rgba(0,0,0,0), rgba(0,0,0,.28) 50%, rgba(0,0,0,0));
  }
  .front__details { position: absolute; left: 284px; top: 44px; right: 20px; }
  .details__name { font-weight: 700; font-size: 19px; color: var(--ink); }
  .details__role { font-size: 14px; color: var(--ink-muted); margin-bottom: 10px; }
  .details__list { list-style: none; }
  .details__item {
    display: flex; align-items: flex-start; gap: 8px;
    font-size: 10.5px; line-height: 1.45; color: var(--ink-soft); margin-bottom: 5px;
  }
  .details__icon { width: 11px; height: 11px; flex: none; margin-top: 2px; }
  .front__band { position: absolute; left: 0; bottom: 0; width: 100%; height: 54px; }

  /* Back */
  .card--back {
    background: linear-gradient(100deg, var(--dark-1) 0%, var(--dark-2) 45%, var(--dark-1) 70%, var(--dark-3) 100%);
  }
  .back__texture {
    position: absolute; inset: 0;
    background: linear-gradient(160deg, rgba(255,255,255,0) 40%, rgba(255,255,255,.12) 60%, rgba(255,255,255,0) 80%);
  }
  .back__brand {
    position: absolute; left: 0; right: 0; top: 70px;
    text-align: center;
  }
  .back__tagline {
    font-size: 10px; font-weight: 600; letter-spacing: 3px; text-transform: uppercase;
    color: rgba(20,20,20,.75); margin-bottom: 10px;
  }
  .back__name {
    display: inline-flex; align-items: center; gap: 12px;
    font-weight: 800; font-size: 30px; color: rgba(20,20,20,.8);
  }
  .back__name .brand__square { background: rgba(20,20,20,.8); width: 22px; height: 22px; }
  .back__url-tab {
    position: absolute; left: 50%; bottom: 0; transform: translateX(-50%);
    width: 280px; height: 38px;
    border-radius: 12px 12px 0 0;
    background: linear-gradient(to bottom, #9a9a9a, #4a4a4a);
    display: flex; align-items: center; justify-content: center;
    font-weight: 700; font-size: 13px; color: #ffffff;
  }
</style>
</head>
<body>

  <section class="card card--front" aria-label="Business card front">
    <div class="front__brand">
      <span class="brand__square"></span>
      <span class="brand__name">Birchway Canine Training</span>
    </div>

    <div class="front__divider"></div>

    <div class="front__details">
      <p class="details__name">Lowell Spratt</p>
      <p class="details__role">Designation</p>
      <ul class="details__list">
        <li class="details__item">
          <svg class="details__icon" viewBox="0 0 12 12"><circle cx="6" cy="6" r="6" fill="#555"/><path d="M6 2.5a2 2 0 0 0-2 2c0 1.6 2 4 2 4s2-2.4 2-4a2 2 0 0 0-2-2z" fill="#fff"/></svg>
          <span>#000 Sample Road, Birchfield, Victoria, 0000, Australia</span>
        </li>
        <li class="details__item">
          <svg class="details__icon" viewBox="0 0 12 12"><circle cx="6" cy="6" r="6" fill="#555"/><path d="M4 3h1.3l.6 1.5-.8.6a4 4 0 0 0 1.8 1.8l.6-.8L9 6.7V8a1 1 0 0 1-1 1A5 5 0 0 1 3 4a1 1 0 0 1 1-1z" fill="#fff"/></svg>
          <span>281-904-3376</span>
        </li>
        <li class="details__item">
          <svg class="details__icon" viewBox="0 0 12 12"><circle cx="6" cy="6" r="6" fill="#555"/><rect x="3" y="4" width="6" height="4.2" fill="#fff"/><path d="M3 4l3 2.3L9 4" stroke="#555" stroke-width=".7" fill="none"/></svg>
          <span>info@birchwaycanine.example</span>
        </li>
        <li class="details__item">
          <svg class="details__icon" viewBox="0 0 12 12"><circle cx="6" cy="6" r="6" fill="#555"/><circle cx="6" cy="6" r="3" stroke="#fff" stroke-width=".8" fill="none"/><path d="M3 6h6M6 3v6" stroke="#fff" stroke-width=".6"/></svg>
          <span>www.birchwaycanine.example</span>
        </li>
      </ul>
    </div>

    <svg class="front__band" viewBox="0 0 525 54" preserveAspectRatio="none" aria-hidden="true">
      <defs>
        <linearGradient id="bandGrad" x1="0" x2="1" y1="0" y2="0">
          <stop offset="0" stop-color="#1e1e1e"/>
          <stop offset=".6" stop-color="#4a4a4a"/>
          <stop offset="1" stop-color="#9a9a9a"/>
        </linearGradient>
      </defs>
      <path d="M0 40 L250 40 L258 30 L420 30 L430 14 L525 14 L525 54 L0 54 Z" fill="url(#bandGrad)"/>
      <path d="M0 40 L250 40 L258 30 L420 30 L430 14 L525 14" stroke="#d8d8d8" stroke-width="2" fill="none"/>
    </svg>
  </section>

  <section class="card card--back" aria-label="Business card back">
    <div class="back__texture" role="img" aria-label="Soft flowing grey light streaks"></div>
    <div class="back__brand">
      <p class="back__tagline">Your dog trainer for life</p>
      <p class="back__name"><span class="brand__square"></span>Birchway Canine Training</p>
    </div>
    <div class="back__url-tab">www.birchwaycanine.example</div>
  </section>

</body>
</html>
```